Federal IT Consulting Company - Brisolux Consulting Group

We're seeking a skilled web designer to create a modern, bold, and engaging WordPress website for Brisolux Consulting Group, LLC. Our company specializes in federal IT consulting, and our name is a play on "Brightening Solutions." The website should reflect our expertise in the federal technology marketplace and position us as a trusted partner for clients navigating their IT journey.

contact: info@brisoluxgrp-example.com

Current Status

WordPress is already installed on our hosting account
We have an existing logo (may need modernization)

Design Requirements

Style:

Modern and visually striking design
Bold elements to convey confidence and expertise
Incorporate the concept of "brightening solutions" into the design

Features:

Modern UX sliders for dynamic content presentation
Eye-catching, high-quality images (stock photos to be sourced by the designer)
Responsive design for all devices

Color Scheme:

To be proposed by the designer, should align with our brand and convey trust and technological expertise

Logo:

Evaluate our current logo
Create a transparent background version if needed
Propose modernization if deemed necessary

Accessibility:

Ensure design elements are accessible to users with disabilities
Use high contrast ratios for text and background colors
Provide text alternatives for non-text content

Website Structure
Create the following pages, with the possibility of subpages:

Home
Services
About
Contact

Specific Page Requirements
Home Page

Striking hero section with a clear value proposition
Overview of our services
Client testimonials or trust indicators

Services Page

Detailed list of our IT consulting services
Clear explanation of how we help navigate the federal IT landscape

About Page

Company history and mission
Team highlights (if applicable)
Our approach to federal IT consulting

Contact Page

Contact form
Other contact methods (phone, email)

Technical Requirements

Fully responsive design
SEO best practices implemented
Fast loading times
Integration with necessary plugins (to be discussed)
Training on how to update and maintain the site
Full compliance with Web Content Accessibility Guidelines (WCAG) 2.1 Level AA
Adherence to Section 508 standards for federal website accessibility
Implementation of necessary features for ADA compliance
Updates

Designs look the same

Target Market(s)

US Federal Govt customers looking for IT support.

Industry/Entity Type

IT Consulting

Coding

Coded - Design and coding required

Colors
0054AA
0677BA
7BADD7
CADEEF
E8F1F8
0094D4
00A9DD
6FCCEA
C7EBF8
E9F6FB
00AB8E
00BBA5
67D7C9
C6EFE9
E9F9F6

```html
<!DOCTYPE html>
<html lang="en">
<head>
<meta charset="utf-8">
<title>Brisolux Consulting Group – Federal IT Consulting</title>
<link href="https://fonts.googleapis.com/css2?family=Outfit:wght@300;400;500;600;700&display=swap" rel="stylesheet">
<style>
:root{
  --blue:#0677BA;
  --blue-deep:#0054AA;
  --sky:#0094D4;
  --accent:#00A9DD;
  --light:#CADEEF;
  --pale:#E8F1F8;
  --navy:#0B2347;
  --navy-2:#0F2D57;
  --ink:#101828;
  --text:#3b4556;
  --white:#ffffff;
}
*{box-sizing:border-box;margin:0;padding:0}
html,body{width:1200px;height:3883px;overflow:hidden}
body{font-family:'Outfit',sans-serif;color:var(--ink);background:var(--white);position:relative}
.abs{position:absolute}
.label{position:absolute;font-size:13px;font-weight:500;letter-spacing:.5px;color:var(--blue-deep);padding-left:8px;border-left:2px solid var(--blue-deep);line-height:16px;text-transform:uppercase}
.label.light{color:#fff;border-color:#fff}
h2{font-weight:500;font-size:29px;line-height:36px;position:absolute}
h2 span{color:var(--sky)}
.btn{position:absolute;display:flex;align-items:center;justify-content:center;font-size:14px;font-weight:500;border-radius:4px;color:#fff;background:var(--sky)}
.photo{position:absolute}

/* nav */
.nav{position:absolute;left:0;top:0;width:1200px;height:70px;background:#fff}
.brand{position:absolute;display:flex;align-items:center;gap:8px;font-weight:600;letter-spacing:1px;color:var(--blue-deep)}
.brand .dot{border-radius:50%;border:4px solid var(--sky)}
.nav-links{position:absolute;right:278px;top:26px;display:flex;gap:36px;font-size:14px;font-weight:500}
.nav-links .on{color:var(--sky)}
/* hero */
.hero{position:absolute;left:0;top:70px;width:1200px;height:487px;background:linear-gradient(100deg,#1d2a4d 0%,#3b3f60 35%,#8a6a66 60%,#c7905f 80%,#6d5a5a 100%)}
.hero h1{position:absolute;left:142px;top:128px;width:385px;font-size:36px;line-height:46px;font-weight:500;color:#fff}
.hero p{position:absolute;left:142px;top:286px;width:300px;font-size:15px;line-height:25px;color:#eef2f8;font-weight:300}
/* about */
.about p{position:absolute;left:638px;width:420px;font-size:12px;line-height:22.5px;color:var(--text)}
/* services */
.band{position:absolute;left:0;top:1431px;width:1200px;height:687px;background:var(--navy)}
.card{position:absolute;top:1256px;width:291px;height:261px;border-radius:8px;overflow:hidden}
.card .glass{position:absolute;left:21px;right:21px;bottom:21px;border-radius:8px;background:rgba(30,45,70,.55);border:1px solid rgba(255,255,255,.7);color:#fff;padding:0 17px}
.card .glass h3{font-size:15px;font-weight:500}
.card .arrow{position:absolute;right:17px;bottom:18px;width:26px;height:26px;border-radius:50%;background:#fff;display:flex;align-items:center;justify-content:center}
.circle-btn{position:absolute;width:38px;height:38px;border-radius:50%;display:flex;align-items:center;justify-content:center}
/* testimonial */
.testi p{position:absolute;left:606px;top:1826px;width:430px;font-size:12.5px;line-height:22.5px;color:#dfe7f2}
/* team */
.member{position:absolute;top:2316px;width:182px;text-align:center}
.member .avatar{width:182px;height:182px;border-radius:50%;background:linear-gradient(180deg,#d6e6f3,#9fb6cc)}
.member h3{font-size:15px;font-weight:600;margin-top:20px}
.member .role{font-size:11px;color:var(--sky);margin-top:4px}
.member .social{display:flex;gap:10px;justify-content:center;margin-top:14px}
.member .social i{width:32px;height:32px;border-radius:50%;background:var(--sky);display:block}
/* cta */
.cta{position:absolute;left:142px;top:2729px;width:916px;height:329px;border-radius:60px;background:linear-gradient(90deg,#0a84cf,#0e93d8)}
/* certs */
.cert{position:absolute;top:3283px;height:183px}
/* footer */
.footer{position:absolute;left:0;top:3550px;width:1200px;height:333px;background:var(--navy)}
.footer h4{position:absolute;top:3624px;font-size:15px;font-weight:500;color:var(--accent)}
.flist{position:absolute;top:3660px;font-size:12.5px;line-height:28px;color:#fff;list-style:none}
.finfo{position:absolute;left:852px;font-size:12.5px;line-height:17px;color:#fff;display:flex;gap:10px}
</style>
</head>
<body>

<!-- Navigation -->
<header class="nav">
  <div class="brand" style="left:142px;top:16px;font-size:26px">
    <span class="dot" style="width:34px;height:34px"></span>Brisolux
  </div>
  <nav class="nav-links"><span class="on">Home</span><span>About Us</span><span>Services</span></nav>
  <a class="btn" style="left:950px;top:14px;width:108px;height:43px;font-size:14px">Contact Us</a>
</header>

<!-- Hero -->
<section class="hero" role="img" aria-label="Dusk view of a domed federal capitol building with a flag">
  <div class="label light" style="left:142px;top:100px">Welcome to Brisolux</div>
  <h1>Navigate Your Federal<br>IT Journey with<br>Confidence.</h1>
  <p>Expert Consulting Services to Guide Your<br>IT Strategy.</p>
  <a class="btn" style="left:142px;top:364px;width:170px;height:42px;background:var(--blue-deep)">Explore Our Services</a>
  <a class="btn" style="left:326px;top:364px;width:190px;height:42px;background:transparent;border:1px solid #fff">Get A Free Consultation</a>
</section>

<!-- About -->
<section class="about">
  <div class="abs" style="left:142px;top:642px;width:82px;height:82px;border-radius:50%;background:var(--pale)"></div>
  <div class="photo" role="img" aria-label="Consultant presenting data on a monitor to a team" style="left:179px;top:681px;width:304px;height:323px;border-radius:10px;background:linear-gradient(160deg,#c9ced6,#7d8797 60%,#4c5566)"></div>
  <div class="photo" role="img" aria-label="Team working together at laptops in an office" style="left:400px;top:878px;width:152px;height:144px;border-radius:10px;background:linear-gradient(160deg,#6e7e8f,#2d3a4b);border:4px solid #fff"></div>
  <div class="label" style="left:638px;top:689px">About Us</div>
  <h2 style="left:638px;top:716px">Why Choose <span>Brisolux?</span></h2>
  <p style="top:776px">There are many variations of passages of Lorem Ipsum available, but the majority have suffered alteration in some form, by injected humour, or randomised words which don't look even slightly believable. If you are going to use a passage of Lorem Ipsum, you need to be sure there isn't anything embarrassing hidden in the middle of text.</p>
  <p style="top:904px">It is a long established fact that a reader will be distracted by the readable content of a page when looking at its layout.</p>
  <a class="btn" style="left:638px;top:972px;width:112px;height:43px">Learn More</a>
</section>

<!-- Services -->
<section class="services">
  <div class="label" style="left:142px;top:1109px">Popular Services</div>
  <h2 style="left:142px;top:1136px">The Best Solution For<br>Your <span>Business</span></h2>
  <a class="btn" style="left:957px;top:1164px;width:101px;height:40px">View All</a>
  <div class="band"></div>
  <svg class="abs" style="left:1010px;top:1550px" width="180" height="180" viewBox="0 0 180 180" aria-hidden="true"><circle cx="90" cy="90" r="62" fill="none" stroke="#183a66" stroke-width="24"/></svg>

  <article class="card" style="left:142px" role="img" aria-label="Cybersecurity operator at monitors">
    <div style="position:absolute;inset:0;background:linear-gradient(160deg,#3a2f5a,#1a2540 60%,#0f1a30)"></div>
    <div class="glass" style="height:124px;padding-top:18px">
      <h3>Cybersecurity</h3>
      <p style="font-size:12px;line-height:18px;margin-top:10px;width:170px;color:#e3e9f2">There are many variations of passages of Lorem Ipsum available.</p>
      <span class="arrow"><svg width="12" height="12" viewBox="0 0 12 12"><path d="M3 9 9 3M4 3h5v5" stroke="#0094D4" stroke-width="1.5" fill="none"/></svg></span>
    </div>
  </article>
  <article class="card" style="left:454px" role="img" aria-label="Hand touching a glowing cloud interface">
    <div style="position:absolute;inset:0;background:linear-gradient(160deg,#2f5a80,#16304f 60%,#0d1f38)"></div>
    <div class="glass" style="height:62px;display:flex;align-items:center"><h3>Cloud Services</h3>
      <span class="arrow" style="bottom:18px"><svg width="12" height="12" viewBox="0 0 12 12"><path d="M3 9 9 3M4 3h5v5" stroke="#0094D4" stroke-width="1.5" fill="none"/></svg></span></div>
  </article>
  <article class="card" style="left:766px" role="img" aria-label="People working at laptops in a bright room">
    <div style="position:absolute;inset:0;background:linear-gradient(160deg,#b39060,#6e5a44 55%,#3a3a40)"></div>
    <div class="glass" style="height:62px;display:flex;align-items:center"><h3>IT Strategy Consulting</h3>
      <span class="arrow" style="bottom:18px"><svg width="12" height="12" viewBox="0 0 12 12"><path d="M3 9 9 3M4 3h5v5" stroke="#0094D4" stroke-width="1.5" fill="none"/></svg></span></div>
  </article>

  <span class="circle-btn" style="left:549px;top:1550px;border:1.5px solid var(--sky)"><svg width="16" height="12" viewBox="0 0 16 12"><path d="M15 6H2M6 2 2 6l4 4" stroke="#0094D4" stroke-width="1.6" fill="none"/></svg></span>
  <span class="circle-btn" style="left:613px;top:1550px;background:var(--sky)"><svg width="16" height="12" viewBox="0 0 16 12"><path d="M1 6h13M10 2l4 4-4 4" stroke="#fff" stroke-width="1.6" fill="none"/></svg></span>
</section>

<!-- Testimonials -->
<section class="testi">
  <div class="photo" role="img" aria-label="Business team reviewing work at a laptop" style="left:0;top:1673px;width:521px;height:445px;background:linear-gradient(150deg,#2a5aa0,#34507a 40%,#6a6a70 70%,#3b3c44)"></div>
  <span class="abs" style="left:231px;top:1866px;width:58px;height:58px;background:var(--blue-deep);display:flex;align-items:center;justify-content:center"><svg width="20" height="22" viewBox="0 0 20 22"><path d="M2 1v20l17-10z" fill="#fff"/></svg></span>
  <div class="abs" style="left:314px;top:2022px;width:249px;height:73px;background:#fff;border-radius:8px;box-shadow:0 6px 20px rgba(0,0,0,.15)">
    <div style="position:absolute;left:22px;top:20px;font-size:13px;font-weight:500;line-height:17px">250+ Global<br>Clients</div>
    <span style="position:absolute;left:126px;top:20px;width:32px;height:32px;border-radius:50%;background:#d98a6a;border:2px solid #fff"></span>
    <span style="position:absolute;left:146px;top:20px;width:32px;height:32px;border-radius:50%;background:#9a5a4a;border:2px solid #fff"></span>
    <span style="position:absolute;left:166px;top:20px;width:32px;height:32px;border-radius:50%;background:#c04040;border:2px solid #fff"></span>
    <span style="position:absolute;left:186px;top:20px;width:34px;height:34px;border-radius:50%;background:var(--sky);border:2px solid #fff;color:#fff;font-size:18px;display:flex;align-items:center;justify-content:center">+</span>
  </div>
  <div class="label light" style="left:606px;top:1693px">Our Testimonials</div>
  <h2 style="left:606px;top:1721px;color:#fff">Hear What Our <span>Clients Say</span></h2>
  <svg class="abs" style="left:606px;top:1790px" width="100" height="16" viewBox="0 0 100 16" aria-label="Five star rating"><g fill="#F7B500"><path id="s" d="M8 0l2.4 5 5.4.6-4 3.7 1.1 5.4L8 12 3.1 14.7 4.2 9.3.2 5.6 5.6 5z"/><use href="#s" x="20"/><use href="#s" x="40"/><use href="#s" x="60"/><use href="#s" x="80"/></g></svg>
  <p>It is a long established fact that a reader will be distracted by the readable content of a page when looking at its layout. The point of using Lorem Ipsum is that it has a more-or-less normal distribution of letters, as opposed to using 'Content here, content here', making it look like readable English.</p>
  <div class="abs" style="left:606px;top:1950px;width:426px;height:1px;background:#6b7d98"></div>
  <span class="abs" style="left:907px;top:1932px;width:38px;height:38px;border-radius:50%;background:var(--navy);border:1.5px solid #cfd8e6;color:#fff;font-size:26px;line-height:44px;text-align:center;font-weight:700">”</span>
  <div class="abs" style="left:606px;top:1984px;width:56px;height:56px;border-radius:50%;background:linear-gradient(160deg,#c8ccd2,#6c737c);border:2px solid #fff"></div>
  <div class="abs" style="left:676px;top:1988px;color:#fff;font-size:15px;font-weight:500">Gerald T. Vantreece</div>
  <div class="abs" style="left:676px;top:2013px;color:#c9d3e2;font-size:12px">CEO &amp; Founder</div>
</section>

<!-- Team -->
<section class="team">
  <div class="label" style="left:562px;top:2204px">Our Team</div>
  <h2 style="left:0;width:1200px;text-align:center;top:2231px">Meet The Our <span>Experts</span></h2>
  <div class="member" style="left:175px"><div class="avatar" role="img" aria-label="Portrait of team member"></div><h3>Marla Quenby</h3><div class="role">Web Designer</div><div class="social"><i></i><i></i></div></div>
  <div class="member" style="left:397px"><div class="avatar" role="img" aria-label="Portrait of team member"></div><h3>Tobias Renwick</h3><div class="role">Web Designer</div><div class="social"><i></i><i></i></div></div>
  <div class="member" style="left:619px"><div class="avatar" role="img" aria-label="Portrait of team member"></div><h3>Priya Halloran</h3><div class="role">Web Designer</div><div class="social"><i></i><i></i></div></div>
  <div class="member" style="left:842px"><div class="avatar" role="img" aria-label="Portrait of team member"></div><h3>Owen Castellan</h3><div class="role">Web Designer</div><div class="social"><i></i><i></i></div></div>
</section>

<!-- Call to action -->
<section>
  <div class="cta">
    <svg class="abs" style="left:530px;top:40px" width="240" height="240" viewBox="0 0 240 240" aria-hidden="true"><circle cx="120" cy="120" r="88" fill="none" stroke="rgba(255,255,255,.12)" stroke-width="34"/></svg>
    <div class="abs" style="left:55px;top:52px;color:#fff;font-size:28px;font-weight:500;line-height:44px">We Are Federal IT Consulting<br>We Make Future!</div>
    <p class="abs" style="left:55px;top:162px;width:440px;color:#fff;font-size:13px;line-height:22px">There are many variations of passages of Lorem Ipsum<br>available, but the majority have suffered alteration in some form.</p>
    <a class="btn" style="left:55px;top:234px;width:146px;height:40px;background:#fff;color:var(--blue)">Get Started Now</a>
    <svg class="abs" style="left:220px;top:215px" width="120" height="80" viewBox="0 0 120 80" aria-hidden="true"><path d="M10 70c10-20 30-10 40-25s30-20 55-30" stroke="#fff" stroke-dasharray="4 4" fill="none"/><path d="M100 8l16-4-8 16-3-7z" fill="none" stroke="#fff"/></svg>
  </div>
  <div class="photo" role="img" aria-label="Smiling consultant in a beige suit holding a laptop" style="left:680px;top:2660px;width:290px;height:398px;border-radius:140px 140px 0 0;background:linear-gradient(180deg,#e6c9a8,#c9a37e 50%,#8a7360)"></div>
</section>

<!-- Certifications -->
<section>
  <div class="label" style="left:541px;top:3143px">Certifications</div>
  <h2 style="left:0;width:1200px;text-align:center;top:3174px">Certificates Of The Most<br>Popular <span>Brands</span></h2>
  <span class="circle-btn" style="left:140px;top:3357px;width:36px;height:36px;border:1.5px solid var(--sky)"><svg width="10" height="14" viewBox="0 0 10 14"><path d="M8 1 2 7l6 6" stroke="#0094D4" stroke-width="1.6" fill="none"/></svg></span>
  <span class="circle-btn" style="left:1023px;top:3357px;width:36px;height:36px;background:var(--sky)"><svg width="10" height="14" viewBox="0 0 10 14"><path d="M2 1l6 6-6 6" stroke="#fff" stroke-width="1.6" fill="none"/></svg></span>
  <div class="cert" role="img" aria-label="Certificate of achievement" style="left:196px;width:254px;background:linear-gradient(160deg,#fbf6ee,#f1e3d0)"></div>
  <div class="cert" role="img" aria-label="Certificate of achievement" style="left:480px;width:241px;background:linear-gradient(160deg,#eef0f3,#c9d0dc)"></div>
  <div class="cert" role="img" aria-label="Certificate of achievement" style="left:752px;width:252px;background:linear-gradient(160deg,#f3f5f9,#c4cee0)"></div>
</section>

<!-- Footer -->
<footer>
  <div class="footer"></div>
  <svg class="abs" style="left:1030px;top:3585px" width="160" height="160" viewBox="0 0 160 160" aria-hidden="true"><circle cx="80" cy="80" r="55" fill="none" stroke="#183a66" stroke-width="22"/></svg>
  <div class="brand" style="left:142px;top:3625px;font-size:40px;color:#fff">
    <span class="dot" style="width:52px;height:52px;border-width:6px"></span>Brisolux
  </div>
  <h4 style="left:511px">Quick Links</h4>
  <ul class="flist" style="left:511px"><li>Home</li><li>About Us</li><li>Services</li></ul>
  <h4 style="left:673px">Resources</h4>
  <ul class="flist" style="left:673px"><li>Privacy Policy</li><li>Terms Of Service</li></ul>
  <h4 style="left:852px">Contact Info</h4>
  <div class="finfo" style="top:3662px"><svg width="16" height="18" viewBox="0 0 16 18"><path d="M8 17s6-6 6-10A6 6 0 0 0 2 7c0 4 6 10 6 10z" fill="none" stroke="#00A9DD" stroke-width="1.6"/><circle cx="8" cy="7" r="2" fill="#00A9DD"/></svg><span>481 Harbor Crest Lane, Suite 210<br>Fairmont Ridge 20145</span></div>
  <div class="finfo" style="top:3711px"><svg width="16" height="12" viewBox="0 0 16 12"><rect x="1" y="1" width="14" height="10" rx="1" fill="#00A9DD"/><path d="M1 2l7 5 7-5" stroke="#0B2347" fill="none"/></svg><span>info@brisoluxgrp-example.com</span></div>
  <div class="finfo" style="top:3745px"><svg width="16" height="16" viewBox="0 0 16 16"><path d="M3 1l3 3-2 2c1 2 3 4 5 5l2-2 3 3-2 3C7 15 1 9 1 3z" fill="#00A9DD"/></svg><span>555-014-2283</span></div>
  <div class="abs" style="left:142px;top:3815px;width:916px;height:1px;background:#2c4670"></div>
  <div class="abs" style="left:142px;top:3843px;font-size:12px;color:#fff">© 2024 Brisolux. All rights reserved.</div>
  <div class="abs" style="left:908px;top:3838px;display:flex;gap:14px" aria-label="Social media links">
    <i style="width:27px;height:27px;border-radius:50%;background:var(--sky);display:block"></i>
    <i style="width:27px;height:27px;border-radius:50%;background:var(--sky);display:block"></i>
    <i style="width:27px;height:27px;border-radius:50%;background:var(--sky);display:block"></i>
    <i style="width:27px;height:27px;border-radius:50%;background:var(--sky);display:block"></i>
  </div>
</footer>

</body>
</html>
```